jQuery Mobile CSS for web app

Task Outline:
Create jQuery Mobile themeroller compliant CSS and icons for a mobile web app.
Task Description:
Brindle Solutions are in the process of implementing a new, web based version of their Tessel operations platform.
The web based version of Tessel is built on top of the jQuery Mobile platform and we are looking for a designer to create a jQuery Mobile themeroller compliant CSS theme pack that we can plug into our application. The aim is to remove the standard jQuery Mobile look and feel and to introduce the Brindle branding throughout the new web app.
A number of screenshots are shown in the attached design spec (brindle_solutions.pdf) that show what the current (Windows Mobile 6.5) application looks like, alongside the development version of our new web app.
Deliverables:
• jQuery Mobile (v 1.4.2) themeroller compliant CSS which provides theming for all jQuery Mobile UI components.
• Example html showing how to use the CSS theme (especially where additional html/css classes are required).
• New set of status icons (as listed in attachment)
Inspiration:
See our website for current branding: www.brindle-solutions-demo.net

```html
<!DOCTYPE html>
<html lang="en">
<head>
<meta charset="utf-8">
<title>Brindle Tessel – Search</title>
<link rel="stylesheet" href="https://fonts.googleapis.com/css2?family=Fira+Sans:wght@500;600&family=Open+Sans:wght@400;600;700&display=swap">
<style>
  :root {
    --page-bg: #e6e6e6;
    --status-bg: #454545;
    --status-text: #f2f2f2;
    --brand-red: #e3000f;
    --brand-red-dark: #c4000c;
    --white: #ffffff;
    --field-border: #e2e2e2;
    --text-dark: #333333;
    --text-mid: #444444;
    --tab-orange: #ff9a00;
    --tab-purple: #a41ee0;
    --tab-teal: #00b4c8;
    --button-top: #3c3c3c;
    --button-bottom: #111111;
    --row-top: #ffffff;
    --row-bottom: #f1f1f1;
    --divider: #e0e0e0;
    --chevron: #c8c8c8;
    --footer-gap: #f2f2f2;
    --footer-alt: #ededed;
  }
  * { box-sizing: border-box; margin: 0; padding: 0; }
  html, body {
    width: 853px; height: 1200px; overflow: hidden;
    background: var(--page-bg);
  }
  .app-screen {
    position: absolute; left: 50px; top: 35px;
    width: 752px; height: 1130px;
    background: var(--white);
    overflow: hidden;
    font-family: "Open Sans", Arial, sans-serif;
    box-shadow: 0 4px 18px rgba(0,0,0,.18);
  }
  .status-bar {
    height: 42px; background: var(--status-bg); color: var(--status-text);
    display: flex; align-items: center; justify-content: space-between;
    padding: 0 10px; font-size: 20px; font-weight: 600;
  }
  .status-bar .signal { display: flex; align-items: center; gap: 8px; }
  .status-bar .battery { display: flex; align-items: center; gap: 8px; }
  .app-header {
    height: 120px;
    background: linear-gradient(180deg, var(--brand-red) 0%, var(--brand-red-dark) 100%);
    display: flex; align-items: center; justify-content: center;
  }
  .app-title {
    font-family: "Fira Sans", Arial, sans-serif; font-weight: 500;
    color: var(--white); font-size: 50px; letter-spacing: .5px;
  }
  .search-panel { padding: 30px 58px 0 65px; }
  .search-field {
    height: 85px; border: 2px solid var(--field-border); border-radius: 4px;
    display: flex; align-items: center; padding-left: 38px;
    font-size: 30px; color: var(--text-dark);
  }
  .search-scope {
    display: flex; margin-top: 18px; height: 72px; border-radius: 4px; overflow: hidden;
  }
  .scope-option {
    flex: 1; display: flex; align-items: center; justify-content: center;
    color: var(--white); font-size: 28px; font-weight: 700;
  }
  .scope-serial { background: var(--tab-orange); }
  .scope-item { background: var(--tab-purple); }
  .scope-description { background: var(--tab-teal); }
  .search-button {
    margin-top: 18px; height: 88px; border-radius: 4px;
    background: linear-gradient(180deg, var(--button-top), var(--button-bottom));
    color: var(--white); display: flex; align-items: center; justify-content: center;
    font-family: "Fira Sans", Arial, sans-serif; font-weight: 500; font-size: 40px;
  }
  .result-list { list-style: none; margin-top: 32px; border-top: 2px solid var(--divider); }
  .result-row {
    height: 165px; display: flex; align-items: center; position: relative;
    background: linear-gradient(180deg, var(--row-top), var(--row-bottom));
    border-bottom: 2px solid var(--divider);
  }
  .result-icon { margin-left: 75px; width: 115px; height: 105px; }
  .result-text { margin-left: 48px; }
  .result-number { font-size: 35px; color: var(--text-mid); line-height: 1.3; }
  .result-desc { font-size: 33px; color: var(--text-dark); line-height: 1.4; }
  .result-chevron { position: absolute; right: 40px; top: 50%; transform: translateY(-50%); }
  .footer-gap { height: 28px; background: var(--footer-gap); }
  .nav-footer {
    position: absolute; left: 0; bottom: 0; width: 100%; height: 82px;
    display: flex; border-top: 2px solid var(--divider);
  }
  .nav-button {
    flex: 1; display: flex; align-items: center; justify-content: center; gap: 10px;
    font-size: 34px; color: var(--text-dark);
  }
  .nav-back { background: var(--white); }
  .nav-next { background: var(--footer-alt); }
</style>
</head>
<body>
<main class="app-screen">
  <div class="status-bar">
    <span class="signal">
      <svg width="34" height="18" viewBox="0 0 34 18"><rect x="0" y="12" width="5" height="6" fill="#f2f2f2"/><rect x="7" y="8" width="5" height="10" fill="#f2f2f2"/><rect x="14" y="4" width="5" height="14" fill="#f2f2f2"/><rect x="21" y="0" width="5" height="18" fill="#f2f2f2"/></svg>
      3G
    </span>
    <span class="clock">8:33 PM</span>
    <span class="battery">99%
      <svg width="46" height="22" viewBox="0 0 46 22"><rect x="1" y="1" width="40" height="20" rx="3" fill="none" stroke="#f2f2f2" stroke-width="2"/><rect x="4" y="4" width="34" height="14" fill="#f2f2f2"/><rect x="42" y="7" width="3" height="8" fill="#f2f2f2"/></svg>
    </span>
  </div>

  <header class="app-header"><h1 class="app-title">Brindle Tessel</h1></header>

  <section class="search-panel">
    <div class="search-field">Cable</div>
    <div class="search-scope">
      <span class="scope-option scope-serial">Serial Nu</span>
      <span class="scope-option scope-item">Item Num</span>
      <span class="scope-option scope-description">Description</span>
    </div>
    <div class="search-button">Search Now</div>
  </section>

  <ul class="result-list">
    <li class="result-row">
      <svg class="result-icon" viewBox="0 0 46 42"><rect x="0" y="0" width="46" height="10" fill="#f08c00"/><rect x="3" y="10" width="40" height="32" fill="#ffd000"/><path d="M18 10h10v17l-5-4-5 4z" fill="#fff"/><path d="M20 10h6v12l-3-2.5-3 2.5z" fill="#ffd000"/></svg>
      <div class="result-text"><div class="result-number">31582</div><div class="result-desc">Morbi diam mauris viver</div></div>
      <svg class="result-chevron" width="40" height="84" viewBox="0 0 40 84"><path d="M3 3l34 39-34 39" fill="none" stroke="#c8c8c8" stroke-width="3"/></svg>
    </li>
    <li class="result-row">
      <svg class="result-icon" viewBox="0 0 46 42"><rect x="0" y="0" width="46" height="10" fill="#1ec8f0"/><rect x="3" y="10" width="40" height="32" fill="#1e8cf0"/><path d="M18 10h10v17l-5-4-5 4z" fill="#fff"/><path d="M20 10h6v12l-3-2.5-3 2.5z" fill="#1e8cf0"/></svg>
      <div class="result-text"><div class="result-number">31577</div><div class="result-desc">Curabitur iaculis tempus</div></div>
      <svg class="result-chevron" width="40" height="84" viewBox="0 0 40 84"><path d="M3 3l34 39-34 39" fill="none" stroke="#c8c8c8" stroke-width="3"/></svg>
    </li>
    <li class="result-row">
      <svg class="result-icon" viewBox="0 0 46 42"><rect x="0" y="0" width="46" height="10" fill="#8c14dc"/><rect x="3" y="10" width="40" height="32" fill="#c814f0"/><path d="M18 10h10v17l-5-4-5 4z" fill="#fff"/><path d="M20 10h6v12l-3-2.5-3 2.5z" fill="#c814f0"/></svg>
      <div class="result-text"><div class="result-number">31285</div><div class="result-desc">Feugiat suscipit leo</div></div>
      <svg class="result-chevron" width="40" height="84" viewBox="0 0 40 84"><path d="M3 3l34 39-34 39" fill="none" stroke="#c8c8c8" stroke-width="3"/></svg>
    </li>
  </ul>
  <div class="footer-gap"></div>

  <nav class="nav-footer">
    <span class="nav-button nav-back">
      <svg width="38" height="38" viewBox="0 0 38 38"><circle cx="19" cy="19" r="16" fill="none" stroke="#333" stroke-width="3"/><path d="M27 19H13M19 12l-7 7 7 7" fill="none" stroke="#333" stroke-width="3.5"/></svg>
      Back
    </span>
    <span class="nav-button nav-next">
      Next
      <svg width="38" height="38" viewBox="0 0 38 38"><circle cx="19" cy="19" r="16" fill="none" stroke="#333" stroke-width="3"/><path d="M11 19h14M19 12l7 7-7 7" fill="none" stroke="#333" stroke-width="3.5"/></svg>
    </span>
  </nav>
</main>
</body>
</html>
```